Brightmill Data Works

Our company is about IT hardwares and IT solutions. IT hardware such as PC, RAMS, storage and servers. IT solutions such as project management, BA. We are also selling new technology too.

Target Market(s)

Consumer, Small to Medium Business, Corporate

Requirements
Must have
• The business card must have the following:
• Name:
• Title:
• Contact Number:
• Email address:
• Website:
• Color: Must match the logo color upgrade

```html
<!DOCTYPE html>
<html lang="en">
<head>
<meta charset="utf-8">
<title>Brightmill Data Works – Business Card</title>
<link rel="stylesheet" href="https://fonts.googleapis.com/css2?family=Rubik:wght@400;500;700&display=swap">
<style>
  :root {
    --bg: #2b2c2e;
    --orange-light: #e09a45;
    --orange-mid: #c9782c;
    --orange-dark: #a85a22;
    --white: #ffffff;
    --ink: #3a3b3d;
    --silver: #dcdcdc;
  }
  * { margin: 0; padding: 0; box-sizing: border-box; }
  html, body { width: 1200px; height: 900px; overflow: hidden; }
  body {
    background: var(--bg);
    font-family: "Rubik", sans-serif;
    display: flex;
    flex-direction: column;
    align-items: center;
    justify-content: center;
    gap: 60px;
  }
  .card {
    position: relative;
    width: 630px;
    height: 360px;
    border-radius: 22px;
    overflow: hidden;
    background: linear-gradient(125deg, var(--orange-dark) 0%, var(--orange-mid) 45%, var(--orange-light) 100%);
    box-shadow: 0 14px 30px rgba(0,0,0,0.45);
  }
  .card-front .panel {
    position: absolute;
    inset: 0;
  }
  .contact {
    position: absolute;
    left: 38px;
    top: 58px;
    color: var(--white);
  }
  .contact .name {
    font-size: 25px;
    font-weight: 500;
    letter-spacing: 0.5px;
    text-transform: uppercase;
  }
  .contact .title {
    font-size: 15px;
    font-weight: 400;
    margin-top: 2px;
    opacity: 0.92;
  }
  .contact .address {
    font-size: 15px;
    line-height: 1.35;
    margin-top: 22px;
  }
  .contact .lines {
    list-style: none;
    margin-top: 14px;
    font-size: 15px;
    line-height: 1.5;
  }
  .contact .lines li { display: flex; align-items: center; gap: 8px; }
  .contact .lines svg { width: 12px; height: 12px; flex: none; }
  .brand-front {
    position: absolute;
    left: 340px;
    top: 150px;
    width: 260px;
    text-align: center;
    color: var(--ink);
    font-weight: 700;
    font-size: 29px;
    line-height: 1.1;
    letter-spacing: 1px;
    text-transform: uppercase;
  }
  .card-back {
    display: flex;
    align-items: center;
    justify-content: center;
  }
  .brand-back {
    color: var(--silver);
    font-weight: 700;
    font-size: 44px;
    letter-spacing: 2px;
    text-transform: uppercase;
    text-align: center;
    line-height: 1.15;
  }
</style>
</head>
<body>
  <section class="card card-front">
    <svg class="panel" viewBox="0 0 630 360" width="630" height="360" aria-hidden="true">
      <path d="M322 0 C 262 110 270 250 360 360" fill="none" stroke="#3f4042" stroke-width="9" stroke-linecap="round"/>
      <path d="M338 0 C 282 110 292 250 378 360 L630 360 L630 0 Z" fill="#ffffff"/>
    </svg>
    <div class="contact">
      <p class="name">Daniel Harlow</p>
      <p class="title">Director</p>
      <p class="address">2250 Orchard Vale Rd<br>Kestrel, CA 95012-4410</p>
      <ul class="lines">
        <li><svg viewBox="0 0 12 12"><path d="M3 1 L5 3.5 L4 5 Q5 7 7 8 L8.5 7 L11 9 L9.5 11 Q4 10.5 1 3 Z" fill="#fff"/></svg>555-014-2277</li>
        <li><svg viewBox="0 0 12 12"><rect x="1" y="2.5" width="10" height="7" fill="none" stroke="#fff" stroke-width="1.2"/><path d="M1 2.5 L6 6.5 L11 2.5" fill="none" stroke="#fff" stroke-width="1.2"/></svg>info@brightmilldata.com</li>
        <li><svg viewBox="0 0 12 12"><circle cx="6" cy="6" r="4.6" fill="none" stroke="#fff" stroke-width="1.2"/><path d="M1.5 6 H10.5 M6 1.5 V10.5" stroke="#fff" stroke-width="1"/></svg>www.brightmilldata.com</li>
      </ul>
    </div>
    <p class="brand-front">Brightmill<br>Data Works</p>
  </section>

  <section class="card card-back">
    <p class="brand-back">Brightmill<br>Data Works</p>
  </section>
</body>
</html>
```